Bry7Legal Letterhead

Need a new letterhead for my law firm.
IDENTIFYING INFORMATION BELOW:
Anselmo R Quintara III
Attorney at Law
Address: 2847 Larkspur Blvd, Ste 300, Dallas, TX 75204
Phone: 877-482-6017
Fax: 469-738-1452
Email: bry@bry7legal.example
Website: www.bry7legal.example

Colors
0054AA
0677BA
7BADD7
CADEEF
E8F1F8

Requirements
Must have
• Logo needs to be on the letterhead, along with identifying information which is included in the project description.

```html
<!DOCTYPE html>
<html lang="en">
<head>
<meta charset="utf-8">
<title>Bry7Legal Letterhead</title>
<link rel="stylesheet" href="https://fonts.googleapis.com/css2?family=Poppins:wght@300;500;700&family=Source+Sans+3:wght@400&display=swap">
<style>
  :root {
    --backdrop: #e2e2e2;
    --paper: #ffffff;
    --ink: #111111;
    --body-ink: #2b2b2b;
    --brand-blue: #0054aa;
    --brand-mid: #0677ba;
    --brand-light: #7badd7;
    --brand-pale: #cadeef;
    --brand-mist: #e8f1f8;
  }
  * { box-sizing: border-box; margin: 0; padding: 0; }
  html, body { width: 1200px; height: 1200px; overflow: hidden; }
  body { background: var(--backdrop); position: relative; }

  .letterhead {
    position: absolute; left: 204px; top: 40px;
    width: 792px; height: 1120px;
    background: var(--paper);
    box-shadow: 0 2px 10px rgba(0,0,0,0.08);
  }

  .brand {
    position: absolute; left: 73px; top: 66px;
    display: flex; align-items: center; gap: 12px;
  }
  .brand-mark { width: 30px; height: 30px; background: var(--brand-blue); }
  .brand-name {
    font-family: "Poppins", sans-serif; font-weight: 500;
    font-size: 32px; line-height: 40px; color: var(--ink);
  }

  .attorney { position: absolute; right: 70px; top: 83px; text-align: right; }
  .attorney-name {
    font-family: "Poppins", sans-serif; font-weight: 700;
    font-size: 13.5px; color: var(--brand-blue); text-transform: uppercase;
  }
  .attorney-title {
    font-family: "Poppins", sans-serif; font-weight: 300;
    font-size: 10px; letter-spacing: 1.5px; color: var(--ink);
    text-transform: uppercase; margin-top: 2px;
  }

  .letter-text { font-family: "Source Sans 3", sans-serif; color: var(--body-ink); font-size: 16.5px; }
  .recipient { position: absolute; left: 75px; top: 268px; line-height: 19.2px; }
  .salutation { position: absolute; left: 75px; top: 408px; }
  .letter-body { position: absolute; left: 75px; top: 453px; width: 680px; line-height: 24px; white-space: nowrap; }
  .closing { position: absolute; left: 75px; top: 804px; }
  .signature {
    position: absolute; left: 73px; top: 845px; width: 138px; height: 70px;
    background: linear-gradient(135deg, #f3f3f3, #e6e6e6); border-radius: 4px;
  }

  .contact-band {
    position: absolute; left: 0; top: 1049px; width: 100%; height: 22px;
    background: linear-gradient(90deg, var(--brand-blue) 0%, var(--brand-mid) 30%, #1591cf 55%, var(--brand-mid) 80%, var(--brand-blue) 100%);
    display: flex; justify-content: center; align-items: center; gap: 18px;
    font-family: "Poppins", sans-serif; font-weight: 300; font-size: 12px; color: #fff;
  }
  .contact-item { display: flex; align-items: center; gap: 3px; white-space: nowrap; }
  .contact-item svg { width: 11px; height: 11px; }
  .office-address {
    position: absolute; left: 0; top: 1076px; width: 100%; text-align: center;
    font-family: "Poppins", sans-serif; font-weight: 500; font-size: 14px; color: var(--ink);
  }
</style>
</head>
<body>
  <main class="letterhead">
    <header>
      <div class="brand">
        <span class="brand-mark" aria-hidden="true"></span>
        <span class="brand-name">Bry7Legal</span>
      </div>
      <div class="attorney">
        <div class="attorney-name">Anselmo R Quintara III</div>
        <div class="attorney-title">Attorney at Law</div>
      </div>
    </header>

    <div class="letter-text recipient">
      Mr. John Doe<br>President<br>Strategy Accountants<br>111 Street Name,<br>City State, 12345
    </div>

    <div class="letter-text salutation">Dear :</div>

    <div class="letter-text letter-body">
      Lorem ipsum dolor sit amet, consectetur adipiscing elit. Aenean ut ipsum eget massa<br>
      hendrerit vestibulum vel in velit. Donec pretium neque velit.<br>
      Aliquam porta lectus nec mauris ornare venenatis. Vivamus non est turpis, et cursus sem.<br>
      Mauris vehicula erat in diam auctor at bibendum nisl lacinia.<br>
      Morbi imperdiet neque vehicula nunc convallis gravida. Vestibulum iaculis pretium placerat.<br>
      Integer consequat, est sit amet facilisis eleifend, nibh nibh varius orci, eget dapibus arcu dui<br>
      non purus. Pellentesque in magna mauris. Duis enim sapien, dictum vitae condimentum a,<br>
      pulvinar vel lacus. Mauris et molestie nibh. Vestibulum vitae nulla at metus elementum<br>
      porta sit amet interdum elit. Nulla sollicitudin neque eu nulla volutpat congue.<br>
      Etiam pellentesque, velit id dapibus fermentum, turpis sapien ornare dui, ac tincidunt ligula<br>
      odio congue purus. Nunc sed ante dui, in porta lectus. Cras nec sem lorem. In hac habitasse<br>
      platea dictumst. Maecenas id diam quis dui porta tristique. Sed id egestas felis. Donec<br>
      ullamcorper mattis posuere. Phasellus fermentum eleifend tortor vel dapibus. Vestibulum<br>
      ante ipsum.
    </div>

    <div class="letter-text closing">Sincerely,</div>
    <div class="signature" role="img" aria-label="Handwritten signature of the attorney"></div>

    <footer>
      <div class="contact-band">
        <span class="contact-item">
          <svg viewBox="0 0 12 12" fill="#fff" aria-hidden="true"><path d="M2.5 1l2 2.3-1 1.2a7 7 0 0 0 4 4l1.2-1 2.3 2-1.3 1.5C5.5 11 1 6.5 1 2.3z"/></svg>877-482-6017
        </span>
        <span class="contact-item">
          <svg viewBox="0 0 12 12" fill="#fff" aria-hidden="true"><rect x="3" y="1" width="6" height="3"/><rect x="1" y="4.5" width="10" height="4.5" rx="1"/><rect x="3" y="8" width="6" height="3"/></svg>469-738-1452
        </span>
        <span class="contact-item">
          <svg viewBox="0 0 12 12" fill="none" stroke="#fff" stroke-width="1.2" aria-hidden="true"><rect x="1" y="2.5" width="10" height="7"/><path d="M1 2.5l5 4 5-4"/></svg>bry@bry7legal.example
        </span>
        <span class="contact-item">
          <svg viewBox="0 0 12 12" fill="none" stroke="#fff" stroke-width="1" aria-hidden="true"><circle cx="6" cy="6" r="5"/><ellipse cx="6" cy="6" rx="2.2" ry="5"/><path d="M1 6h10M2 3.5h8M2 8.5h8"/></svg>www.bry7legal.example
        </span>
      </div>
      <div class="office-address">2847 Larkspur Blvd, Ste 300, Dallas, TX 75204</div>
    </footer>
  </main>
</body>
</html>
```